Veltrona Pocket Folder

Create a new pocket folder
An Overview / Background of the Business & Services
We would like a new folder to use when making formal presentations
* The Target Market / Audience you are trying to reach
The target audience are commercial businesses that we are selling group insurance products to
* Design Specifics; any preferences or ideas for Style, Colour, Imagery, etc
We wanted to use the Houston, Texas skyline and create something that was simple, yet modern.
* Do you have an existing website or Facebook page were designers can learn more about your company?
Yes, http://www.veltronagroup.example and we are on Linked-In.
Updates
Project Deadline Extended Reason: We have many people who have to agree. We need to get an answer on the form of the ready art we will receive when we select a designer .Thank you. Added Thursday, April 27, 2017
Industry/Entity Type
Business
Look and feel
Each slider illustrates characteristics of the customer's brand and the style your logo design should communicate.

```html
<!DOCTYPE html>
<html lang="en">
<head>
<meta charset="utf-8">
<title>Veltrona Pocket Folder</title>
<link href="https://fonts.googleapis.com/css2?family=Open+Sans:wght@400;600;700&display=swap" rel="stylesheet">
<style>
  :root {
    --stage: #bdbcbd;
    --paper: #ffffff;
    --blue-light: #04a3e2;
    --blue-mid: #0489cc;
    --blue-deep: #0a5f97;
    --sky-top: #9fa2a1;
    --sky-low: #5d625f;
    --brand-grey: #6d6e71;
  }
  * { margin: 0; padding: 0; box-sizing: border-box; }
  html, body { width: 1200px; height: 1200px; overflow: hidden; }
  body {
    background: var(--stage);
    font-family: "Open Sans", Arial, sans-serif;
    display: flex;
    align-items: center;
    justify-content: center;
  }
  .folder-spread {
    display: flex;
    box-shadow: 0 18px 40px rgba(0,0,0,0.25);
  }
  .panel {
    position: relative;
    width: 510px;
    height: 680px;
    overflow: hidden;
  }
  .panel-art { position: absolute; inset: 0; display: block; }

  /* Back cover */
  .back-contact {
    position: absolute;
    left: 0; right: 0;
    bottom: 58px;
    color: var(--paper);
    text-align: center;
  }
  .wordmark {
    display: inline-flex;
    align-items: center;
    gap: 9px;
    font-weight: 700;
    letter-spacing: 0.2px;
  }
  .wordmark-square { display: inline-block; border-radius: 3px; }
  .back-contact .wordmark { font-size: 25px; color: var(--paper); }
  .back-contact .wordmark-square { width: 24px; height: 24px; background: var(--paper); }
  .contact-columns {
    margin-top: 10px;
    display: flex;
    justify-content: center;
    align-items: stretch;
    gap: 12px;
    font-size: 11px;
    line-height: 1.45;
  }
  .contact-address { text-align: right; }
  .contact-address .company { font-weight: 700; }
  .contact-divider { width: 1px; background: var(--paper); }
  .contact-lines { text-align: left; list-style: none; }
  .contact-lines li { display: flex; align-items: center; gap: 6px; }
  .contact-lines svg { width: 10px; height: 10px; flex: none; }

  /* Front cover */
  .front-brand {
    position: absolute;
    top: 95px;
    left: 0; right: 0;
    text-align: center;
  }
  .front-brand .wordmark { font-size: 50px; color: var(--brand-grey); gap: 16px; }
  .front-brand .wordmark-square { width: 54px; height: 54px; background: var(--blue-mid); }
</style>
</head>
<body>
  <main class="folder-spread">
    <section class="panel back-cover">
      <svg class="panel-art" viewBox="0 0 510 680" preserveAspectRatio="none">
        <defs>
          <linearGradient id="backBlue" x1="0" y1="0" x2="1" y2="0">
            <stop offset="0" stop-color="var(--blue-mid)"/>
            <stop offset="1" stop-color="var(--blue-deep)"/>
          </linearGradient>
          <linearGradient id="skyline" x1="0" y1="0" x2="0" y2="1">
            <stop offset="0" stop-color="var(--sky-top)"/>
            <stop offset="1" stop-color="var(--sky-low)"/>
          </linearGradient>
        </defs>
        <rect width="510" height="680" fill="url(#backBlue)"/>
        <path d="M0 0 H510 V228 Q260 270 0 300 Z" fill="var(--paper)" opacity="0.9"/>
        <path d="M0 0 H510 V220 Q260 262 0 292 Z" fill="url(#skyline)" role="img" aria-label="Aerial photograph of the Houston city skyline"/>
      </svg>
      <div class="back-contact">
        <div class="wordmark"><span class="wordmark-square"></span>Veltrona</div>
        <div class="contact-columns">
          <address class="contact-address" style="font-style:normal">
            <div class="company">Veltrona Corporation</div>
            <div>4820 Meridian Park Drive, Suite 210</div>
            <div>Houston, TX 77042</div>
          </address>
          <span class="contact-divider"></span>
          <ul class="contact-lines">
            <li><svg viewBox="0 0 10 10"><path d="M2 1 L4 1 L4.5 3 L3.3 4 Q4.5 6 6 6.7 L7 5.5 L9 6 L9 8 Q5 9 2 6 Q0.5 3.5 2 1Z" fill="#fff"/></svg>713-555-0148</li>
            <li><svg viewBox="0 0 10 10"><rect x="0.5" y="2" width="9" height="6" fill="none" stroke="#fff"/><path d="M0.5 2 L5 5.5 L9.5 2" fill="none" stroke="#fff"/></svg>info@veltronagroup.example</li>
            <li><svg viewBox="0 0 10 10"><circle cx="5" cy="5" r="4.3" fill="none" stroke="#fff"/><ellipse cx="5" cy="5" rx="1.8" ry="4.3" fill="none" stroke="#fff"/><path d="M0.7 5 H9.3" stroke="#fff"/></svg>www.veltronagroup.example</li>
          </ul>
        </div>
      </div>
    </section>

    <section class="panel front-cover">
      <svg class="panel-art" viewBox="0 0 510 680" preserveAspectRatio="none">
        <defs>
          <linearGradient id="frontBlue" x1="0" y1="0" x2="1" y2="0.4">
            <stop offset="0" stop-color="var(--blue-light)"/>
            <stop offset="1" stop-color="var(--blue-deep)"/>
          </linearGradient>
        </defs>
        <rect width="510" height="680" fill="var(--paper)"/>
        <rect y="238" width="510" height="442" fill="url(#frontBlue)"/>
      </svg>
      <div class="front-brand">
        <div class="wordmark"><span class="wordmark-square"></span>Veltrona</div>
      </div>
    </section>
  </main>
</body>
</html>
```